Business Card Design and Logo Needed

I need Business Cards and a Logo for my website and public speaking business which can be found at: www.corvina-lett.example

I'm looking for creative and unique ideas. Some business cards I've found online that I like can be found at:
http://gigbarrow.example/general/18-smokin-hot-business-card-designs/

and at

http://www.plumquarry.example/2009/04/50-creative-business-cards-of-50-graphic-designers/

```html
<!DOCTYPE html>
<html lang="en">
<head>
<meta charset="utf-8">
<title>Corvina Lett – Business Card</title>
<link rel="stylesheet" href="https://fonts.googleapis.com/css2?family=Raleway:wght@300&display=swap">
<style>
  :root {
    --olive: #41520f;
    --paper: #ffffff;
    --faint-lime: #edf3d6;
  }
  * { box-sizing: border-box; margin: 0; padding: 0; }
  html, body {
    width: 1200px;
    height: 900px;
    overflow: hidden;
    background: var(--paper);
  }
  .canvas {
    position: relative;
    width: 1200px;
    height: 900px;
    font-family: "Raleway", Arial, sans-serif;
    font-weight: 300;
  }
  .card {
    position: absolute;
    left: 234px;
    width: 742px;
    height: 372px;
    overflow: hidden;
  }
  .card--front {
    top: 34px;
    background: var(--olive);
    color: var(--paper);
    text-align: center;
  }
  .wordmark {
    position: absolute;
    top: 150px;
    left: 0;
    right: 0;
    font-size: 84px;
    line-height: 1;
    letter-spacing: 1px;
    font-weight: 300;
  }
  .tagline {
    position: absolute;
    top: 262px;
    left: 0;
    right: 0;
    font-size: 20px;
    line-height: 1.2;
    letter-spacing: 1px;
  }
  .card--back {
    top: 490px;
    background: var(--paper);
    border: 2px solid var(--olive);
    color: var(--olive);
  }
  .back-motto {
    position: absolute;
    top: 34px;
    left: 38px;
    font-size: 16px;
    color: var(--faint-lime);
    letter-spacing: 1px;
  }
  .contact {
    position: absolute;
    left: 0;
    right: 0;
    text-align: center;
    font-size: 22px;
    line-height: 1.2;
    letter-spacing: 0.5px;
  }
  .contact--phone { top: 170px; }
  .contact--email { top: 254px; }
  .contact--web { top: 294px; }
</style>
</head>
<body>
  <main class="canvas">
    <section class="card card--front" aria-label="Business card front">
      <h1 class="wordmark">CORVINA LETT</h1>
      <p class="tagline">public speaker</p>
    </section>

    <section class="card card--back" aria-label="Business card back">
      <p class="back-motto">speaker author mentor coach</p>
      <p class="contact contact--phone">0147 238 560</p>
      <p class="contact contact--email">corvina@corvina-lett.example</p>
      <p class="contact contact--web">www.corvina-lett.example</p>
    </section>
  </main>
</body>
</html>
```